Graphic design on webpages considering optimisation

Hi,

I would like to make the pages of my website look better. The looks must tie with the landing page, which I will not change.

Ping me an email with any questions. I have been on Pixel Harbour for the brimtower.com page and am very pleased with its looks.

Industry/Entity Type

Graphic Design

```html
<!DOCTYPE html>
<html lang="en">
<head>
<meta charset="utf-8">
<title>Brimtower – Added values</title>
<link rel="stylesheet" href="https://fonts.googleapis.com/css2?family=Roboto:wght@400;500;700&family=Roboto+Slab:wght@400&display=swap">
<style>
:root{
  --blue:#0d4fb5;
  --navy:#1a3c8c;
  --text:#555;
  --heading:#1b4a9c;
  --bullet-red:#8c1a1a;
  --bullet-green:#6e9a3a;
  --grey-line:#d6d6d6;
  --side-bg:#f0f0f0;
  --green-btn:#7fb24d;
  --orange-btn:#f0911c;
  --footer:#111;
}
*{box-sizing:border-box;margin:0;padding:0}
html,body{width:1200px;height:2329px;overflow:hidden;background:#fff}
body{position:relative;font-family:"Roboto",Arial,sans-serif;color:var(--text)}
.abs{position:absolute}
.brand{left:199px;top:36px;font:700 28px/1 "Roboto",sans-serif;color:#4a4a4a;letter-spacing:2px;display:flex;align-items:center;gap:10px}
.brand-dot{width:14px;height:14px;background:var(--blue);border-radius:50%}
.phone{right:201px;top:42px;font:400 20px/1 "Roboto",sans-serif;color:var(--blue);display:flex;align-items:center;gap:8px}
.nav{left:199px;top:99px;width:800px;height:39px;background:linear-gradient(#2f86ee,#0b4fbd);display:flex}
.nav a{flex:1;color:#fff;text-decoration:none;font-size:11px;display:flex;align-items:center;justify-content:center;border-right:1px solid rgba(255,255,255,.25)}
.nav a:last-child{border-right:0}
.hero{left:199px;top:138px;width:800px;height:256px;background:linear-gradient(90deg,#d9d4cf 0%,#c8c4c0 35%,#a9aaad 70%,#8f9196 100%)}
.hero-arrow{top:226px;color:#fff;font-size:34px;line-height:1}
.hero-dots{left:578px;top:376px;display:flex;gap:3px}
.hero-dots i{width:10px;height:10px;border-radius:50%;border:2px solid var(--navy);background:#fff}
.hero-dots i:first-child{background:var(--navy)}
.side{left:199px;top:424px;width:170px}
.side-head{background:var(--blue);color:#fff;font-size:10px;height:28px;display:flex;align-items:center;justify-content:center}
.side-list{list-style:none;border:1px solid var(--grey-line);border-top:0}
.side-list li{height:28px;display:flex;align-items:center;justify-content:center;font-size:10px;color:#777;background:var(--side-bg);border-top:1px solid #fff}
.info-title{left:199px;top:624px;font-size:15px;color:var(--heading)}
.btn{left:199px;width:166px;height:36px;border-radius:7px;color:#fff;font-size:13px;display:flex;align-items:center;justify-content:center}
.btn-contact{top:655px;background:var(--green-btn)}
.btn-quote{top:703px;background:var(--orange-btn)}
.partner-head{left:199px;top:763px;width:170px;height:26px;background:var(--blue);color:#fff;font-size:13px;padding-left:8px;display:flex;align-items:center}
.partner-box{left:199px;top:789px;width:170px;height:65px;border:1px solid var(--grey-line);display:flex;align-items:center;justify-content:center}
.partner-box span{width:110px;height:30px;background:#1e3552;opacity:.85}
.main{left:385px;top:424px;width:614px;font-size:9.6px;line-height:17.6px}
.main h1{font:400 21px/1.2 "Roboto Slab",serif;color:var(--heading);margin-bottom:8px}
.main h2{font-size:11px;font-weight:400;color:var(--heading);margin:12px 0 14px}
.list{list-style:none;padding-left:14px}
.list>li{position:relative;padding-left:14px;margin-bottom:14px}
.list>li::before{content:"";position:absolute;left:0;top:4px;border-left:6px solid var(--bullet-red);border-top:5px solid transparent;border-bottom:5px solid transparent}
.sub{list-style:none;padding-left:30px;margin-top:16px}
.sub li{position:relative;padding-left:14px;margin-bottom:10px}
.sub li::before{content:"";position:absolute;left:0;top:4px;border-left:6px solid var(--bullet-green);border-top:5px solid transparent;border-bottom:5px solid transparent}
.product{color:var(--bullet-red)}
.section-tag{left:199px;width:139px;height:28px;background:var(--blue);color:#fff;font-size:13px;display:flex;align-items:center;justify-content:center}
.clients{left:234px;top:1808px;width:741px;height:186px;display:flex;border:1px solid var(--grey-line)}
.client{flex:1;border-right:1px solid var(--grey-line);padding:12px 12px 8px;display:flex;flex-direction:column;align-items:center}
.client:last-child{border-right:0}
.client-name{font:700 11px/1 "Roboto",sans-serif;color:#222;margin-bottom:4px}
.client-shot{width:110px;height:86px;background:linear-gradient(#e9e4de,#b9b2aa)}
.client-note{font:9px/1.2 "Roboto Slab",serif;color:#222;text-align:center;margin-top:8px}
.benefit{top:2090px;width:183px;height:129px;border:1px solid var(--grey-line);display:flex;flex-direction:column;align-items:center;padding-top:14px}
.cloud{width:96px;height:60px;border-radius:30px;background:linear-gradient(#dfeef8,#9fc8e6)}
.benefit-label{margin-top:10px;width:118px;height:20px;background:#cfe3ee;border-radius:3px;display:flex;align-items:center;justify-content:space-between;padding:0 4px 0 8px;font-size:9px;color:var(--navy)}
.play{width:20px;height:14px;background:#222;display:flex;align-items:center;justify-content:center}
.play::after{content:"";border-left:6px solid #fff;border-top:4px solid transparent;border-bottom:4px solid transparent}
.footer{left:0;top:2252px;width:1200px;height:77px;background:var(--footer);color:#fff;font-size:11px}
.copyright{left:199px;top:33px}
.social{left:898px;top:25px;display:flex;gap:6px}
.social i{width:26px;height:26px;border-radius:50%;background:#d9d9d9}
</style>
</head>
<body>
<header>
  <div class="abs brand"><span>BRIMTOWER</span><span class="brand-dot"></span></div>
  <div class="abs phone">
    <svg width="20" height="20" viewBox="0 0 24 24"><path fill="#111" d="M6.6 10.8a15 15 0 0 0 6.6 6.6l2.2-2.2a1 1 0 0 1 1-.25 11.4 11.4 0 0 0 3.6.6 1 1 0 0 1 1 1V20a1 1 0 0 1-1 1A17 17 0 0 1 3 4a1 1 0 0 1 1-1h3.5a1 1 0 0 1 1 1c0 1.25.2 2.45.6 3.6a1 1 0 0 1-.25 1z"/></svg>
    +33 (0) 100 555 010
  </div>
  <nav class="abs nav">
    <a>Accueil</a><a>Products Valeur</a><a>Ajoutees</a><a>Clients</a><a>Services</a><a>Societe</a><a>Contact</a>
  </nav>
  <div class="abs hero" role="img" aria-label="Photo of a man touching a virtual interface on a grey background"></div>
  <div class="abs hero-arrow" style="left:230px">&#8249;</div>
  <div class="abs hero-arrow" style="left:954px">&#8250;</div>
  <div class="abs hero-dots"><i></i><i></i><i></i></div>
</header>

<aside>
  <div class="abs side">
    <div class="side-head">Nos Services</div>
    <ul class="side-list"><li>Conseil</li><li>Support</li><li>Development</li><li>Formation</li><li>Decouverte</li></ul>
  </div>
  <div class="abs info-title">An info?</div>
  <div class="abs btn btn-contact">Contactez nous</div>
  <div class="abs btn btn-quote">Demende De Devis</div>
  <div class="abs partner-head">Our Partnerships</div>
  <div class="abs partner-box"><span></span></div>
</aside>

<main class="abs main">
  <h1>Added values</h1>
  <p>The vast majority of you today is already equipped with management software, then we can legitimately ask: why change?</p>
  <p>Because LedgerSuite software suite brings real benefits, as will be detailed below ... and illustrate personalized to your case if you leave us a few details in the following form: complete the form</p>
  <h2>Common to all LedgerSuite product benefits :</h2>
  <ul class="list">
    <li>LedgerSuite software is accessible via internet called SaaS or that is in the cloud mode. Unless you will not be equipped (which is extremely rare) or your Internet Service Provider fails to provide a reasonable rate, you'll enjoy.</li>
    <li>A hyper competitive price for the use of an ERP (whether ERP, e-commerce, CRM, LedgerSuite Multisite): indeed, in the price that is offered is that LedgerSuite handles all machine part, administration, backup, repair, any interventions on the operating system or application (except for any specific developments you'd like), equipment such as machine room, air conditioning, technical staff, licenses, updates, maintenance (technical support in English as standard, contact us for technical support in French) ... hence the savings .</li>
    <li>A reactivity unusual thanks to internet access, any electronic, PC, Mac, tablets, smartphones, ... anywhere (area covered by internet or mobile networks), at any time .</li>
    <li>Of savings consistent with the optimization of the operational functioning: regardless of the chosen, for example, just the finance accounting, automated processes Module provide speed processing, low error rates, reduced time billing and payment , where positive financial impacts or another example by managing multi-channel multi-site inventory, regardless of the product purchased by one of your channels (physical outlets, online sale, sale indirectly through distributors, ...), the stock is updated in real time simulations based on historical sales, correct your vision experienced manager, avoid stockouts while maintaining the optimum level.</li>
    <li>A rapid generalized to all that touches the LedgerSuite software: besides the financial aspect is the satisfaction before any of your customers (and employees who are affected) that will emerge grown. With automated processes (workflows), procedures for processing and approval consistent with good practices from around the world and any customizations you want to make, everything is accelerated , lost time avoided the demeaning tasks difficult or replaced by more time and attention devoted to customer service.</li>
    <li>A productivity tenfold thanks to real-time information system, providing centralized data while shared and accessible anytime, anywhere, on multiple media (browsers, tablets, smartphones), dependable, unique, easy to obtain.</li>
    <li>A peace of mind found thanks to the reliability of the information system</li>
    <li>A faculty decision phenomenal thanks to the 360 ° obtained in real time on full, fair, timely. Releasing makers demeaning or time-consuming tasks and providing the 360 ° on the activity, LedgerSuite software allow them to make the right strategic choices and support the successful implementation of these choices.</li>
    <li>A turnover and profitability increased by maximizing the customer relationship: in all stages of the service to the Customer, his first contact with the order and beyond, by its retention, LedgerSuite software provides the most . For example:
      <ul class="sub">
        <li>With the identification of the user behavior or buying habits of the customer, the company can offer complementary products that match their needs</li>
        <li>With the acceleration of the delivery period the Customer's order, obtained by better management of multi-site and appropriate replenishment stocks, a fluidity of the process from ordering to billing and delivery, integration with providers and carriers, a fair billing and clear even in complex control and visibility into the reality of things, the company takes its time and retains its Client</li>
        <li>With custom profiles Guest as volume price reductions granted to the deserving clients or promotions on items remaining too long in stocks and corresponding potential clients wishes of some proposals, the company can optimize a customer account</li>
        <li>With the identification of the best selling products, the company can negotiate better conditions of purchase from their suppliers and increase its margins and / or increase sales</li>
        <li>With secure access to the right level of information (order status, purchase volume, delivery) by the Customer or Partner self-service, the company can retain a customer while minimizing time-consuming telephone interactions and resources</li>
        <li>Through increased collaboration between real-time internal and external services that work on the same data, the best service is delivered to Customer.</li>
      </ul>
    </li>
  </ul>
  <h2>Specific benefits :</h2>
  <ul class="list">
    <li><span class="product">LedgerSuite CRM +:</span>
      <ul class="sub">
        <li>With visibility across the entire interaction (technical problems reassembled unresolved disputes or claims pending, undelivered orders, payment incidents, volume purchasing, interests, ...) between their clients and their business, collaborative work within and among organizations (positive reference product category for example, a product photo, quote a Client feedback from a colleague ...), business can adopt the most appropriate behavior to optimize their business relationships</li>
        <li>Through automation of time-consuming tasks such as developing sales forecasts and quick and easy ad-hoc statistics on the effectiveness of marketing campaigns supply salespeople can focus on the good exploration fields.</li>
      </ul>
    </li>
    <li><span class="product">LedgerSuite E-Commerce:</span>
      <ul class="sub">
        <li>By taking into account interactions Client Web and mobile channel, the upstream visibility Guest strengthens, to knowingly solicit a contact database, through targeted marketing campaigns to their needs.</li>
        <li>Thanks to the E-Commerce solution LedgerSuite, ease of implementation and its integration with all LedgerSuite software, the company can optimize all of its operational and strategic operation, reduce vulnerabilities and increase its strengths.</li>
      </ul>
    </li>
  </ul>
</main>

<section>
  <div class="abs section-tag" style="top:1755px">Customer benefits</div>
  <div class="abs clients">
    <div class="client"><div class="client-name">Sunbrook</div><div class="client-shot" role="img" aria-label="Screenshot of a client website"></div><div class="client-note">Revenue from 85 to 130, delivery time cut 25%</div></div>
    <div class="client"><div class="client-name">Clearwell</div><div class="client-shot" role="img" aria-label="Screenshot of a client website"></div><div class="client-note">95% growth, same staff, 40% storage freed</div></div>
    <div class="client"><div class="client-name">Ridgeline Outfitters</div><div class="client-shot" role="img" aria-label="Screenshot of a client website"></div><div class="client-note">Revenue x10, from 20 to 300 retailers</div></div>
    <div class="client"><div class="client-name">petalpost.com</div><div class="client-shot" role="img" aria-label="Screenshot of a client website"></div><div class="client-note">30K saved, 20% lower costs, live stock view</div></div>
    <div class="client"><div class="client-name">Tidewave Robotics</div><div class="client-shot" role="img" aria-label="Screenshot of a client website"></div><div class="client-note">Planning in 10h instead of 100h, revenue x3</div></div>
  </div>

  <div class="abs section-tag" style="top:2033px">LedgerSuite benefits</div>
  <div class="abs benefit" style="left:199px"><div class="cloud" role="img" aria-label="Cloud illustration with gears"></div><div class="benefit-label">Manufacturing<span class="play"></span></div></div>
  <div class="abs benefit" style="left:406px"><div class="cloud" role="img" aria-label="Cloud illustration with a delivery truck"></div><div class="benefit-label">Distribution<span class="play"></span></div></div>
  <div class="abs benefit" style="left:610px"><div class="cloud" role="img" aria-label="Cloud illustration with a handshake"></div><div class="benefit-label">Services<span class="play"></span></div></div>
  <div class="abs benefit" style="left:818px"><div class="cloud" role="img" aria-label="Cloud illustration with a magnifying glass"></div><div class="benefit-label">Host or not?<span class="play"></span></div></div>
</section>

<footer class="abs footer">
  <div class="abs copyright">© 2014 Brimtower All Rights Reserved</div>
  <div class="abs social"><i></i><i></i><i></i></div>
</footer>
</body>
</html>
```